Animal Eye Clinic needs a Business card

We are a new veterinary ophthalmology practice (Ridgeline Pet Vision Care) and we need a business card designed. We only see animal eyes - we are not a regular veterinary clinic. We already have a logo. We are looking for a professional, good looking business card to hand out to our clients. We are looking for something simple but professional and contemporary. Our logo is likely the only picture/graphic that needs to be on the card.
Updates

Contact Information for Business Card

Delia Vossman, BSc, DVM, MSc, DipACVO
Veterinary Ophthalmologist

Phone: 250.418.3927
Email: ridgelinepetvisioncare@mailbox-example.net
Website: ridgelinepetvisioncare-example.net
Address: 1874 Thornbury Rd
Kelowna, BC, V1X 4M9

Colors

Designer to choose colors to be used in the design.

Requirements
Must have
• Our logo (attached)

```html
<!DOCTYPE html>
<html lang="en">
<head>
<meta charset="utf-8">
<title>Ridgeline Pet Vision Care – Business Card</title>
<link href="https://fonts.googleapis.com/css2?family=Open+Sans:wght@400&family=Roboto:wght@500;700&display=swap" rel="stylesheet">
<style>
  :root {
    --teal: #279fae;
    --charcoal: #58585a;
    --text-grey: #5f5f61;
    --rule-grey: #8a8a8c;
    --paper: #ffffff;
    --backdrop: #e6e2dc;
  }
  * { margin: 0; padding: 0; box-sizing: border-box; }
  html, body { width: 900px; height: 1200px; overflow: hidden; }
  body { background: var(--backdrop); position: relative; font-family: "Open Sans", sans-serif; }

  .card {
    position: absolute;
    left: 86px;
    width: 736px;
    height: 430px;
    box-shadow: 0 3px 10px rgba(0,0,0,0.25);
  }
  .card-front { top: 137px; background: var(--paper); }
  .card-back { top: 633px; background: var(--charcoal); }

  .brand {
    position: absolute;
    left: 0; right: 0;
    display: flex;
    align-items: center;
    justify-content: center;
    gap: 14px;
  }
  .brand-dot { border-radius: 50%; background: var(--teal); flex: none; }
  .brand-name {
    font-family: "Roboto", sans-serif;
    font-weight: 700;
    color: var(--teal);
    white-space: nowrap;
  }
  .card-front .brand { top: 82px; }
  .card-front .brand-dot { width: 38px; height: 38px; }
  .card-front .brand-name { font-size: 29px; }

  .card-back .brand { top: 190px; gap: 20px; }
  .card-back .brand-dot { width: 58px; height: 58px; }
  .card-back .brand-name { font-size: 42px; }

  .person {
    position: absolute;
    top: 220px; left: 0; right: 0;
    text-align: center;
  }
  .person-name {
    font-family: "Roboto", sans-serif;
    font-weight: 700;
    font-size: 31px;
    line-height: 32px;
    color: var(--teal);
  }
  .person-credentials, .person-title {
    font-size: 16px;
    line-height: 17px;
    letter-spacing: 0.6px;
    color: var(--text-grey);
  }

  .rule { position: absolute; height: 1px; background: var(--rule-grey); }
  .rule-left { top: 273px; left: 26px; width: 219px; }
  .rule-right { top: 273px; left: 490px; width: 220px; }
  .rule-bottom { top: 374px; left: 26px; width: 684px; }

  .divider { position: absolute; top: 295px; width: 1px; height: 62px; background: var(--teal); }
  .divider-1 { left: 156px; }
  .divider-2 { left: 461px; }

  .contact {
    position: absolute;
    top: 302px;
    text-align: center;
    color: var(--text-grey);
    font-size: 15px;
    white-space: nowrap;
  }
  .contact svg { display: block; margin: 0 auto 10px; width: 22px; height: 22px; }
  .contact-phone { left: 26px; width: 130px; }
  .contact-email { left: 157px; width: 304px; font-size: 12.5px; padding-top: 2px; }
  .contact-web { left: 462px; width: 248px; font-size: 13.5px; }

  .address-band {
    position: absolute;
    top: 378px; left: 26px;
    width: 684px; height: 26px;
    background: var(--teal);
    color: var(--paper);
    font-size: 15.5px;
    line-height: 26px;
    text-align: center;
  }
</style>
</head>
<body>

<section class="card card-front">
  <div class="brand">
    <span class="brand-dot"></span>
    <span class="brand-name">RIDGELINE PET VISION CARE</span>
  </div>

  <div class="person">
    <div class="person-name">DELIA VOSSMAN</div>
    <div class="person-credentials">BSc, DVM, MSc, DipACVO</div>
    <div class="person-title">Veterinary Ophthalmologist</div>
  </div>

  <div class="rule rule-left"></div>
  <div class="rule rule-right"></div>

  <div class="contact contact-phone">
    <svg viewBox="0 0 24 24" aria-hidden="true"><path fill="#279fae" d="M6.6 10.8c1.4 2.8 3.8 5.1 6.6 6.6l2.2-2.2c.3-.3.7-.4 1-.2 1.1.4 2.3.6 3.6.6.6 0 1 .4 1 1V20c0 .6-.4 1-1 1C10.6 21 3 13.4 3 4c0-.6.4-1 1-1h3.5c.6 0 1 .4 1 1 0 1.3.2 2.5.6 3.6.1.3 0 .7-.2 1l-2.3 2.2z"/></svg>
    250.418.3927
  </div>
  <div class="divider divider-1"></div>
  <div class="contact contact-email">
    <svg viewBox="0 0 24 24" aria-hidden="true"><rect x="2.5" y="5" width="19" height="14" rx="2" fill="none" stroke="#279fae" stroke-width="2"/><path d="M3 6l9 7 9-7" fill="none" stroke="#279fae" stroke-width="2"/></svg>
    ridgelinepetvisioncare@mailbox-example.net
  </div>
  <div class="divider divider-2"></div>
  <div class="contact contact-web">
    <svg viewBox="0 0 24 24" aria-hidden="true" fill="none" stroke="#279fae" stroke-width="1.6"><circle cx="12" cy="12" r="9.5"/><ellipse cx="12" cy="12" rx="4.2" ry="9.5"/><path d="M2.5 12h19M4 7h16M4 17h16M12 2.5v19"/></svg>
    ridgelinepetvisioncare-example.net
  </div>

  <div class="rule rule-bottom"></div>
  <div class="address-band">1874 Thornbury Rd, Kelowna, BC, V1X 4M9</div>
</section>

<section class="card card-back">
  <div class="brand">
    <span class="brand-dot"></span>
    <span class="brand-name">RIDGELINE PET VISION CARE</span>
  </div>
</section>

</body>
</html>
```